Heron Loan Partners Business Card

We need a business card design for our mortgage servicing company. In addition to servicing the loans of homeowners, we help homeowners with purchasing their homes and any mortgage refinancing. We would like to see designs that use the colors in the logo attached below (gold-ish yellow and navy blue), and any other design you deem fit! The design should communicate a simpler life with smart mortgages provided by Heron.

```html
<!DOCTYPE html>
<html lang="en">
<head>
<meta charset="utf-8">
<title>Heron Loan Partners Business Card</title>
<link href="https://fonts.googleapis.com/css2?family=Arimo:wght@400;700&display=swap" rel="stylesheet">
<style>
  :root {
    --gold: #cca434;
    --navy: #1f1a4e;
    --paper: #f5f5f5;
    --ink: #2a2a2a;
    --stage: #e9e7e3;
  }
  * { margin: 0; padding: 0; box-sizing: border-box; }
  html, body { width: 1200px; height: 912px; overflow: hidden; }
  body {
    background: var(--stage);
    font-family: "Arimo", Arial, sans-serif;
    position: relative;
  }
  .card {
    position: absolute;
    width: 560px;
    height: 320px;
    box-shadow: 0 10px 30px rgba(0,0,0,0.18);
    overflow: hidden;
  }
  .card-back { left: 60px; top: 80px; background: var(--gold); }
  .card-front { left: 580px; top: 512px; background: var(--paper); }

  .brand { display: flex; align-items: center; gap: 10px; }
  .brand-mark { width: 14px; height: 14px; border-radius: 50%; background: var(--navy); }
  .brand-name { font-weight: 700; color: var(--navy); letter-spacing: 0.5px; }

  .card-back .brand { position: absolute; left: 0; right: 0; top: 126px; justify-content: center; }
  .card-back .brand-name { font-size: 38px; color: #ffffff; }
  .card-back .brand-mark { background: #ffffff; width: 18px; height: 18px; }
  .card-back .web {
    position: absolute; left: 0; right: 0; top: 230px;
    text-align: center; font-size: 15px; letter-spacing: 3px; color: var(--navy);
  }

  .card-front .brand { position: absolute; right: 40px; top: 46px; }
  .card-front .brand-name { font-size: 24px; color: var(--gold); }
  .card-front .brand-mark { background: var(--gold); width: 12px; height: 12px; }

  .divider {
    position: absolute; left: 34px; right: 40px; top: 186px;
    height: 1px; background: var(--ink);
  }
  .person { position: absolute; left: 34px; top: 130px; }
  .person-name { font-size: 24px; font-weight: 700; color: var(--gold); }
  .person-title { font-size: 16px; color: var(--navy); margin-top: 3px; }
  .address {
    position: absolute; left: 34px; top: 200px;
    font-size: 16px; line-height: 22px; color: var(--ink);
  }
  .contact {
    position: absolute; right: 40px; top: 120px;
    list-style: none; text-align: right;
    font-size: 15px; line-height: 21px; color: var(--ink);
  }
  .contact li { display: flex; justify-content: flex-end; align-items: center; gap: 8px; }
  .contact svg { width: 11px; height: 11px; fill: var(--gold); }

  .rule-navy { position: absolute; left: 0; right: 0; bottom: 30px; height: 3px; background: var(--navy); }
  .band-gold { position: absolute; left: 0; right: 0; bottom: 0; height: 26px; background: var(--gold); }
</style>
</head>
<body>
  <section class="card card-back">
    <div class="brand">
      <span class="brand-mark"></span>
      <span class="brand-name">Heron Loan Partners</span>
    </div>
    <p class="web">www.heronloans.com</p>
  </section>

  <section class="card card-front">
    <div class="brand">
      <span class="brand-mark"></span>
      <span class="brand-name">Heron Loan Partners</span>
    </div>

    <div class="person">
      <p class="person-name">Daniel Reeve</p>
      <p class="person-title">President</p>
    </div>

    <ul class="contact">
      <li>(555) 8416-2790
        <svg viewBox="0 0 12 12"><path d="M2 1h3l1 3-2 1c1 2 2 3 4 4l1-2 3 1v3c-6 0-10-4-10-10z"/></svg>
      </li>
      <li>name@heronloans.com
        <svg viewBox="0 0 12 12"><path d="M0 2h12v8H0z M0 2l6 5 6-5" /></svg>
      </li>
      <li>www.heronloans.com
        <svg viewBox="0 0 12 12"><circle cx="6" cy="6" r="6"/></svg>
      </li>
    </ul>

    <div class="divider"></div>

    <p class="address">4120 Lakeview Drive<br>Bay Harbor, NY 11902</p>

    <div class="rule-navy"></div>
    <div class="band-gold"></div>
  </section>
</body>
</html>
```